Corporate Business Card

Very professional, Modern, Not to busy, include phone address email, website
(253) 617-4930, 18761 52nd Avenue S, Kent, WA 98047, martin@plumlinegroup.com, varkoworks.com

Target Market(s)

Manufacturing

Industry/Entity Type

Aero, machining, manufacturing, Off road racing

Contact Information for Business Card

Phone, address email, website

```html
<!DOCTYPE html>
<html lang="en">
<head>
<meta charset="utf-8">
<title>Varko Works – Business Card</title>
<link href="https://fonts.googleapis.com/css2?family=Roboto:wght@400&family=Saira:wght@600;700&display=swap" rel="stylesheet">
<style>
  :root {
    --stage: #2b2b2b;
    --card-navy: #28366a;
    --card-navy-deep: #22305f;
    --accent-red: #b1202a;
    --steel-grey: #8a8c90;
    --logo-grey: #4a4c52;
    --text-white: #f2f3f6;
    --text-soft: #d9dce6;
  }
  * { box-sizing: border-box; margin: 0; padding: 0; }
  html, body { width: 1200px; height: 1138px; overflow: hidden; }
  body {
    background: var(--stage);
    font-family: "Roboto", Arial, sans-serif;
    position: relative;
  }
  .card {
    position: absolute;
    border-radius: 16px;
    background: linear-gradient(180deg, var(--card-navy) 0%, var(--card-navy-deep) 100%);
    overflow: hidden;
    box-shadow: 0 6px 14px rgba(0,0,0,0.45);
  }
  /* Front side */
  .card-front { left: 274px; top: 186px; width: 623px; height: 376px; }
  .front-wordmark {
    position: absolute; left: 0; right: 0; top: 118px;
    text-align: center;
    font-family: "Saira", Arial, sans-serif;
    font-weight: 700;
    font-size: 64px;
    letter-spacing: 2px;
    color: var(--logo-grey);
  }
  .front-url {
    position: absolute; left: 0; right: 0; top: 326px;
    text-align: center;
    font-size: 16px;
    letter-spacing: 11px;
    color: var(--text-soft);
  }
  .front-url .url-accent { color: var(--accent-red); }

  /* Back side */
  .card-back { left: 276px; top: 608px; width: 618px; height: 374px; }
  .back-wordmark {
    position: absolute; left: 46px; top: 62px;
    font-family: "Saira", Arial, sans-serif;
    font-weight: 700;
    font-size: 52px;
    line-height: 1;
    letter-spacing: 1px;
    color: var(--text-white);
  }
  .holder-name {
    position: absolute; left: 45px; top: 210px;
    font-family: "Saira", Arial, sans-serif;
    font-weight: 700;
    font-size: 25px;
    color: var(--text-white);
    letter-spacing: 0.5px;
  }
  .contact-list {
    position: absolute; left: 45px; top: 248px;
    list-style: none;
  }
  .contact-list li {
    display: flex; align-items: center;
    height: 24.5px;
    font-size: 16.5px;
    color: var(--text-white);
  }
  .contact-list svg { width: 14px; height: 14px; margin-right: 18px; fill: var(--accent-red); }
  .address {
    position: absolute; right: 44px; top: 246px;
    text-align: right;
    font-size: 16.5px;
    line-height: 24px;
    color: var(--text-white);
  }
  .footer-bar { position: absolute; left: 0; bottom: 0; width: 100%; height: 46px; }
  .footer-bar svg { display: block; width: 100%; height: 100%; }
  .company-legal {
    position: absolute; right: 25px; bottom: 9px;
    font-family: "Saira", Arial, sans-serif;
    font-weight: 700;
    font-size: 23px;
    color: var(--text-white);
    letter-spacing: 0.3px;
  }
</style>
</head>
<body>

<section class="card card-front" aria-label="Card front">
  <div class="front-wordmark">VARKO WORKS</div>
  <div class="front-url">www.varko<span class="url-accent">works</span>.com</div>
</section>

<section class="card card-back" aria-label="Card back">
  <div class="back-wordmark">VARKO WORKS</div>

  <div class="holder-name">MARTIN HALE</div>

  <ul class="contact-list">
    <li>
      <svg viewBox="0 0 16 16" aria-hidden="true"><path d="M2 5c0-2 2-3 6-3s6 1 6 3v1h-3V5H5v1H2z M4 7h8l2 7H2z"/></svg>
      (253) 617-4930
    </li>
    <li>
      <svg viewBox="0 0 16 16" aria-hidden="true"><path d="M1 3h14v10H1z" fill="none" stroke="#b1202a" stroke-width="1.6"/><path d="M1 3l7 6 7-6" fill="none" stroke="#b1202a" stroke-width="1.6"/></svg>
      martin@plumlinegroup.com
    </li>
    <li>
      <svg viewBox="0 0 16 16" aria-hidden="true"><circle cx="8" cy="8" r="6.5" fill="none" stroke="#b1202a" stroke-width="1.4"/><path d="M1.5 8h13M8 1.5v13M3 4.5h10M3 11.5h10" stroke="#b1202a" stroke-width="1" fill="none"/></svg>
      www.varkoworks.com
    </li>
  </ul>

  <address class="address" style="font-style:normal">
    18761 52nd Avenue S,<br>
    Kent, WA 98047
  </address>

  <div class="footer-bar">
    <svg viewBox="0 0 618 46" preserveAspectRatio="none" aria-hidden="true">
      <rect x="0" y="32" width="300" height="14" fill="#8a8c90"/>
      <polygon points="300,46 276,46 276,32 300,32" fill="#8a8c90"/>
      <polygon points="292,46 316,0 618,0 618,46" fill="#b1202a"/>
    </svg>
  </div>
  <div class="company-legal">VARKO WORKS LLC</div>
</section>

</body>
</html>
```